Post storm repair flyer

looking for an eye catching 6x9 postcard to send out to single family home owners advertising a "Post Storm Repair Special" explaining that after the recent hurricanes its very important to have your roof checked and any repairs fixed right away before they become a bigger more costly problem and that even though your home wasn't directly hit by the storm the high wind gust could've cause unseen damage.
offer $200 off any repair *some rules may apply
Crest Roofing
877.512.DUNE
www.DuneRoofingco.example

```html
<!DOCTYPE html>
<html lang="en">
<head>
<meta charset="utf-8">
<title>Crest Roofing – Post Storm Repair Special Postcard</title>
<link href="https://fonts.googleapis.com/css2?family=Poppins:wght@400;500;600;700;800;900&display=swap" rel="stylesheet">
<style>
:root{
  --bg:#9a9a9a;
  --card:#ebebea;
  --ink:#1b1b1b;
  --gold:#dcb21f;
  --red:#c8242a;
  --white:#ffffff;
  --sky-top:#f1f2ef;
  --sky-mid:#c9d4c9;
  --hill:#a8b640;
  --hill-dark:#8f9b2c;
}
*{box-sizing:border-box;margin:0;padding:0}
html,body{width:1200px;height:1200px;overflow:hidden}
body{background:var(--bg);font-family:"Poppins",sans-serif;color:var(--ink);position:relative}
.card{position:absolute;left:195px;width:810px;height:540px;overflow:hidden;background:var(--card);box-shadow:0 8px 24px rgba(0,0,0,.25)}
.card--front{top:40px}
.card--back{top:620px}

/* FRONT */
.storm-scene{position:absolute;inset:0;background:linear-gradient(180deg,var(--sky-top) 0%,var(--sky-mid) 38%,#b9c46a 62%,var(--hill) 80%,var(--hill-dark) 100%)}
.brand{position:absolute;top:56px;left:0;width:100%;text-align:center;font-weight:800;font-size:22px;letter-spacing:1px}
.headline{position:absolute;top:110px;left:0;width:100%;text-align:center;font-weight:500;font-size:19px;line-height:1.15}
.headline strong{display:block;font-weight:900;font-size:22px;margin-top:4px}
.special{position:absolute;top:258px;left:50%;transform:translateX(-50%);background:var(--gold);color:var(--white);font-weight:800;font-size:15px;letter-spacing:1px;padding:5px 18px;border-radius:20px;white-space:nowrap}
.storm-note{position:absolute;top:298px;left:145px;width:520px;text-align:center;font-size:12px;line-height:1.35;font-weight:500}
.band{position:absolute;inset:0;width:810px;height:540px}
.offer-tag{position:absolute;left:14px;top:384px;width:300px;height:58px;background:var(--white);border-radius:10px 30px 30px 10px;padding:6px 14px 0 62px;box-shadow:0 2px 6px rgba(0,0,0,.2)}
.offer-badge{position:absolute;left:10px;top:10px;width:38px;height:38px;border-radius:50%;background:var(--gold);color:var(--white);font-weight:800;font-size:16px;display:flex;align-items:center;justify-content:center}
.offer-line{font-size:12px;font-weight:800;color:var(--red);line-height:1.3}
.offer-line b{font-size:17px;font-weight:900}
.offer-rules{font-size:7px;color:#555;line-height:1.2}
.offer-contact{font-size:13px;font-weight:600;line-height:1.3}
.col{position:absolute}
.col h3{font-weight:900;font-size:15px;line-height:1.2;margin-bottom:2px}
.col p{font-size:11px;line-height:1.3}
.col--reach{left:28px;top:456px;width:250px}
.col--refer{left:300px;top:420px;width:250px}
.divider{position:absolute;left:286px;top:424px;width:2px;height:104px;background:var(--white)}
.col--address{left:570px;top:446px;width:230px}
.col--address p{font-size:10.5px}

/* BACK */
.services{position:absolute;left:34px;top:30px;width:345px}
.services h2,.process h2{font-weight:900;font-size:19px;line-height:1.2}
.services p{font-size:11.5px;line-height:1.35;text-align:justify}
.tile{position:absolute;width:118px;height:100px}
.tile-photo{width:100%;height:100%}
.ribbon{position:absolute;background:var(--gold);color:var(--white);font-weight:600;font-size:9px;line-height:1.2;text-align:center;padding:4px 6px;text-transform:uppercase;white-space:nowrap}
.tile--storm{left:60px;top:226px}
.tile--new{left:200px;top:208px}
.tile--retail{left:90px;top:356px}
.tile--repair{left:230px;top:338px}
.tile--storm .tile-photo{background:linear-gradient(160deg,#8a95a5,#6c7584)}
.tile--new .tile-photo{background:linear-gradient(180deg,#6f9bd3 0%,#8b6a48 55%,#5a4632 100%)}
.tile--retail .tile-photo{background:linear-gradient(180deg,#a8b7cc 0%,#7d7f82 55%,#a99a82 100%)}
.tile--repair .tile-photo{background:linear-gradient(180deg,#3f6a3c 0%,#78a9d6 50%,#8c8f93 100%)}
.ribbon--storm{left:-4px;bottom:-16px}
.ribbon--new{left:10px;bottom:-10px}
.ribbon--retail{left:-4px;bottom:-16px}
.ribbon--repair{left:20px;bottom:-14px}
.fold-line{position:absolute;left:412px;top:20px;height:470px;border-left:1.5px dashed #888}
.process{position:absolute;left:440px;top:28px;width:350px}
.steps{list-style:none;margin-top:8px;position:relative;padding-left:30px}
.steps::before{content:"";position:absolute;left:9px;top:10px;bottom:20px;border-left:2px solid var(--gold)}
.steps li{position:relative;font-size:12px;line-height:1.3;margin-bottom:12px}
.step-num{position:absolute;left:-30px;top:2px;width:20px;height:20px;border-radius:50%;background:var(--gold);color:var(--white);font-size:10px;font-weight:700;display:flex;align-items:center;justify-content:center}
.mail-line{position:absolute;left:440px;top:250px;width:340px;border-top:1.5px dashed #888}
.postage{position:absolute;right:30px;top:272px;width:78px;height:78px;border:1.5px solid var(--ink);font-size:7px;font-weight:600;display:flex;align-items:center;justify-content:center;text-align:center;line-height:1.2}
.address-box{position:absolute;left:470px;top:400px;width:270px;height:46px;border:1.5px solid var(--ink);font-size:8px;padding:18px 10px 0;line-height:1.2}
.bottom-band{position:absolute;left:0;bottom:0;width:100%;height:26px;background:var(--gold)}
</style>
</head>
<body>

<section class="card card--front" aria-label="Postcard front">
  <div class="storm-scene" role="img" aria-label="Illustration: storm clouds and two tornadoes over green hills, a damaged house on the left and a protected blue-roofed house inside a glass dome on the right"></div>
  <div class="brand">CREST ROOFING</div>
  <h1 class="headline">You<br>Worked Hard<br>Building Your<br>Home.<strong>PROTECT YOUR NEST!</strong></h1>
  <div class="special">POST STORM REPAIR SPECIAL</div>
  <p class="storm-note">After the recent hurricanes, have your roof checked and repaired right away – before small damage becomes a bigger, more costly problem. Even if the storm didn't hit your home directly, high wind gusts can cause unseen damage.</p>

  <svg class="band" viewBox="0 0 810 540" aria-hidden="true">
    <path d="M0 424 L300 424 L325 396 L500 396 L522 414 L810 382 L810 540 L0 540 Z" fill="var(--gold)"/>
    <path d="M0 424 L300 424 L325 396 L500 396 L522 414 L810 382" fill="none" stroke="var(--white)" stroke-width="3"/>
  </svg>

  <div class="offer-tag">
    <div class="offer-badge">%</div>
    <div class="offer-line">Offer <b>$200</b> Off Any Repair</div>
    <div class="offer-rules">*Some Rules May Apply</div>
    <div class="offer-contact">Crest Roofing, 877.512.DUNE</div>
  </div>

  <div class="col col--reach">
    <h3>REACH US</h3>
    <p>P: 770.555.0142<br>E: info@crestroofing.example<br>W: www.DuneRoofingco.example<br>Serving North Georgia &amp; Surrounding Areas</p>
  </div>
  <div class="divider"></div>
  <div class="col col--refer">
    <h3>REFER US</h3>
    <p>Referrals help build community! Let us earn your referral and we will donate a percentage of proceeds back into our community!</p>
  </div>
  <div class="col col--address">
    <p>Crest Home Group LLC | P : 877.512.DUNE<br>418 Maple Ridge Rd, Ste B2<br>Lakeview, GA 30990<br>www.DuneRoofingco.example</p>
  </div>
</section>

<section class="card card--back" aria-label="Postcard back">
  <div class="services">
    <h2>SERVICES</h2>
    <p>Crest Roofing offers an array of roofing solutions while providing professional, honest recommendations that address your specific needs. You can always count on us for exceptional service from the moment we meet. From inspection to installation, Crest has you covered.</p>
  </div>

  <div class="tile tile--storm">
    <div class="tile-photo" role="img" aria-label="Photo of storm-damaged roof shingles"></div>
    <div class="ribbon ribbon--storm">Storm Damage<br>Roof Replacement</div>
  </div>
  <div class="tile tile--new">
    <div class="tile-photo" role="img" aria-label="Photo of a house under new construction"></div>
    <div class="ribbon ribbon--new">New Construction</div>
  </div>
  <div class="tile tile--retail">
    <div class="tile-photo" role="img" aria-label="Photo of a residential roofline"></div>
    <div class="ribbon ribbon--retail">Retail/Commercial<br>Roof Replacement</div>
  </div>
  <div class="tile tile--repair">
    <div class="tile-photo" role="img" aria-label="Photo of a roof covered with a blue tarp for repair"></div>
    <div class="ribbon ribbon--repair">Repairs &amp;<br>Restoration</div>
  </div>

  <div class="fold-line"></div>

  <div class="process">
    <h2>CREST ROOFING PROCESS</h2>
    <ol class="steps">
      <li><span class="step-num">1</span>Complimentary consultation to assess your roofing need and review our honest recommendations.</li>
      <li><span class="step-num">2</span>Our team of professionals replace, restore, or repair your roof making the process as stress-free as possible.</li>
      <li><span class="step-num">3</span>100% satisfaction, peace of mind, and continued professional coverage backed by Crest Protection*.</li>
    </ol>
  </div>

  <div class="mail-line"></div>
  <div class="postage">U.S POSTAGE<br>EDDM RETAIL</div>
  <div class="address-box">Local<br>Postal Customer</div>
  <div class="bottom-band"></div>
</section>

</body>
</html>
```